Business Card Design

We are a manufacturing and distribution company with most of our customer base being supermarkets. We have established brand guidelines that are attached.

```html
<!DOCTYPE html>
<html lang="en">
<head>
<meta charset="utf-8">
<title>Corvale Business Card</title>
<link href="https://fonts.googleapis.com/css2?family=Poppins:wght@400;600;700&display=swap" rel="stylesheet">
<style>
  :root {
    --backdrop: #2b2b2d;
    --card-white: #ffffff;
    --ink: #1d1d1f;
    --brand-red: #e31e2d;
    --brand-blue: #0a68b4;
    --blue-deep: #075a9f;
    --blue-light: #2a9be6;
    --rule: #9a9a9a;
  }
  * { margin: 0; padding: 0; box-sizing: border-box; }
  html, body {
    width: 1200px; height: 1108px; overflow: hidden;
    background: var(--backdrop);
    font-family: "Poppins", sans-serif;
  }
  .stage {
    position: relative; width: 1200px; height: 1108px;
    display: flex; justify-content: center; align-items: center; gap: 80px;
  }
  .card {
    position: relative; width: 420px; height: 700px;
    border-radius: 28px; overflow: hidden;
  }
  .card-front {
    background: var(--card-white);
    display: flex; flex-direction: column; align-items: center;
    text-align: center; color: var(--ink);
  }
  .brand {
    margin-top: 150px;
    display: flex; flex-direction: column; align-items: center; gap: 22px;
  }
  .brand-square {
    width: 34px; height: 34px; background: var(--brand-red);
  }
  .brand-name {
    font-weight: 700; font-size: 50px; letter-spacing: 2px; line-height: 1;
    color: var(--ink);
  }
  .person { margin-top: 110px; }
  .person-name {
    font-weight: 700; font-size: 27px; letter-spacing: 0.5px; line-height: 1.1;
    text-transform: uppercase;
  }
  .person-first { color: var(--brand-red); }
  .person-last { color: var(--brand-blue); }
  .person-title { font-size: 18px; margin-top: 2px; }
  .icon-row {
    margin-top: 16px; width: 300px;
    display: flex; align-items: center; gap: 8px;
  }
  .icon-row .rule { flex: 1; height: 1px; background: var(--rule); }
  .icon-box {
    width: 32px; height: 32px; border-radius: 7px;
    background: var(--brand-red);
    display: flex; align-items: center; justify-content: center;
  }
  .contact { margin-top: 10px; font-size: 18px; line-height: 1.4; }
  .divider { width: 300px; height: 1px; background: var(--rule); margin: 18px 0 14px; }
  .address { font-size: 17px; line-height: 1.4; }

  .card-back { background: var(--blue-deep); }
  .back-pattern {
    position: absolute; inset: 0;
    background: linear-gradient(215deg, var(--blue-light) 0%, var(--brand-blue) 45%, var(--blue-deep) 100%);
  }
  .back-brand {
    position: absolute; right: 70px; bottom: 200px;
    font-weight: 700; font-size: 22px; letter-spacing: 1px; color: var(--card-white);
  }
</style>
</head>
<body>
<main class="stage">
  <section class="card card-front">
    <div class="brand">
      <span class="brand-square"></span>
      <span class="brand-name">CORVALE</span>
    </div>
    <div class="person">
      <p class="person-name"><span class="person-first">Marcus</span> <span class="person-last">Hale</span></p>
      <p class="person-title">Managing Director</p>
    </div>
    <div class="icon-row">
      <span class="rule"></span>
      <span class="icon-box" aria-label="phone">
        <svg width="18" height="18" viewBox="0 0 24 24"><path fill="#fff" d="M6.6 10.8a15.1 15.1 0 0 0 6.6 6.6l2.2-2.2a1 1 0 0 1 1-.25 11.4 11.4 0 0 0 3.6.57 1 1 0 0 1 1 1V20a1 1 0 0 1-1 1A17 17 0 0 1 3 4a1 1 0 0 1 1-1h3.5a1 1 0 0 1 1 1c0 1.25.2 2.45.57 3.57a1 1 0 0 1-.25 1z"/></svg>
      </span>
      <span class="icon-box" aria-label="email">
        <svg width="18" height="18" viewBox="0 0 24 24"><rect x="3" y="5" width="18" height="14" rx="1" fill="none" stroke="#fff" stroke-width="2"/><path d="M3 6l9 7 9-7" fill="none" stroke="#fff" stroke-width="2"/></svg>
      </span>
      <span class="icon-box" aria-label="website">
        <svg width="18" height="18" viewBox="0 0 24 24"><circle cx="12" cy="12" r="9" fill="none" stroke="#fff" stroke-width="2"/><path d="M3 12h18M12 3c3 3 3 15 0 18M12 3c-3 3-3 15 0 18" fill="none" stroke="#fff" stroke-width="1.6"/></svg>
      </span>
      <span class="rule"></span>
    </div>
    <div class="contact">
      <p>044-987 654 321</p>
      <p>hello@corvale.com</p>
      <p>www.corvale.com</p>
    </div>
    <div class="divider"></div>
    <div class="address">
      <p>18, Harbour Road Millbrook</p>
      <p>30217, Westland</p>
    </div>
  </section>

  <section class="card card-back">
    <div class="back-pattern" role="img" aria-label="Repeating embossed brand pattern in tones of blue"></div>
    <span class="back-brand">CORVALE</span>
  </section>
</main>
</body>
</html>
```